All-Natural Head Lice Removal company

I need a business card with my pre-existing logo. We are a new company located in Portland Oregon that goes into peoples homes to help with head lice removal. My products and approach are all- natural and also will be around children.On my current logo we used Teal Bl and the color Green. I am open to new ideas just want it simple and creative

Target Market(s)

my biggest market is families of school aged children

Industry/Entity Type

Business

Contact Information for Business Card

see upload for details from previous business card

Font styles to use
Serif

Colors
33a6d7
9bcb3b
f37122

Requirements
Must have
• Basic information/ logo put into a creative format that is catching to the eye
Nice to have
• creative

```html
<!DOCTYPE html>
<html lang="en">
<head>
<meta charset="utf-8">
<title>Clear Crown – Business Card</title>
<link rel="stylesheet" href="https://fonts.googleapis.com/css2?family=Arvo:wght@400;700&family=Open+Sans:wght@400;600&display=swap">
<style>
  :root {
    --teal: #33a6d7;
    --leaf: #9bcb3b;
    --ink: #1c1c1c;
    --band: #161616;
    --paper: #ffffff;
    --stage: #e9e7e3;
    --muted: #d9d9d9;
  }
  * { box-sizing: border-box; margin: 0; padding: 0; }
  html, body { width: 1200px; height: 913px; overflow: hidden; }
  body { background: var(--stage); position: relative; }

  .card {
    position: absolute;
    width: 540px;
    height: 309px;
    background: var(--paper);
    overflow: hidden;
    box-shadow: 0 6px 18px rgba(0,0,0,.18);
  }
  .card--front { left: 60px; top: 120px; }
  .card--back  { left: 600px; top: 480px; }

  .card__shapes { position: absolute; inset: 0; width: 540px; height: 309px; }

  .tagline {
    position: absolute;
    left: 26px; top: 27px;
    font: 700 15px "Arvo", serif;
    color: var(--ink);
  }

  .brand-name {
    position: absolute;
    font: 700 20px "Arvo", serif;
    color: var(--paper);
    white-space: nowrap;
  }
  .card--front .brand-name { left: 445px; top: 180px; transform: translateX(-50%); }

  .contact { position: absolute; left: 30px; top: 220px; color: var(--paper); }
  .contact__name { font: 400 19px "Arvo", serif; letter-spacing: .5px; text-transform: uppercase; line-height: 22px; }
  .contact__role { font: 400 11px "Arvo", serif; color: var(--teal); text-transform: uppercase; letter-spacing: 1px; line-height: 16px; }
  .contact__line { display: flex; align-items: center; gap: 7px; font: 400 12px "Open Sans", sans-serif; line-height: 15px; }
  .contact__line svg { width: 10px; height: 10px; flex: none; }

  .back-brand { position: absolute; left: 0; right: 0; top: 56px; display: flex; justify-content: center; align-items: center; gap: 14px; }
  .back-brand__dot { width: 80px; height: 80px; border-radius: 50%; background: var(--leaf); }
  .back-brand__name { font: 700 32px "Arvo", serif; color: var(--ink); }

  .back-tagline {
    position: absolute; left: 0; right: 0; top: 172px;
    text-align: center;
    font: 700 14px "Arvo", serif;
    color: var(--ink);
    line-height: 20px;
  }
  .back-band {
    position: absolute; left: 0; right: 0; top: 228px; height: 34px;
    background: var(--band);
    border-bottom: 4px solid var(--muted);
    display: flex; align-items: center; justify-content: center;
    font: 700 13px "Arvo", serif; color: var(--paper); letter-spacing: .5px;
  }
</style>
</head>
<body>

<section class="card card--front" aria-label="Business card front">
  <svg class="card__shapes" viewBox="0 0 540 309" aria-hidden="true">
    <rect x="0" y="30" width="14" height="14" fill="var(--teal)"/>
    <polygon points="0,213 540,75 540,81 0,219" fill="var(--teal)"/>
    <polygon points="0,222 540,84 540,309 0,309" fill="var(--band)"/>
    <circle cx="445" cy="112" r="56" fill="var(--leaf)"/>
  </svg>

  <p class="tagline">All Natural In-Home Lice Removal Services</p>
  <p class="brand-name">Clear Crown</p>

  <div class="contact">
    <p class="contact__name">Maren Holloway</p>
    <p class="contact__role">Owner</p>
    <p class="contact__line">
      <svg viewBox="0 0 10 10" aria-hidden="true"><path d="M2 0.5 L4 2.5 L3 3.8 Q4.5 6 6.2 7 L7.5 6 L9.5 8 L8 9.5 Q3 9 0.5 2 Z" fill="var(--teal)"/></svg>
      1-800-555-0199
    </p>
    <p class="contact__line">
      <svg viewBox="0 0 10 10" aria-hidden="true"><rect x="0.7" y="2" width="8.6" height="6" fill="none" stroke="var(--teal)" stroke-width="1.2"/><path d="M0.7 2 L5 5.5 L9.3 2" fill="none" stroke="var(--teal)" stroke-width="1.2"/></svg>
      Maren@ClearCrownCare.com
    </p>
    <p class="contact__line">
      <svg viewBox="0 0 10 10" aria-hidden="true"><circle cx="5" cy="5" r="4.3" fill="none" stroke="var(--teal)" stroke-width="1.1"/><ellipse cx="5" cy="5" rx="1.8" ry="4.3" fill="none" stroke="var(--teal)" stroke-width="1"/><line x1="0.7" y1="5" x2="9.3" y2="5" stroke="var(--teal)" stroke-width="1"/></svg>
      www.ClearCrownCare.com
    </p>
  </div>
</section>

<section class="card card--back" aria-label="Business card back">
  <div class="back-brand">
    <span class="back-brand__dot" aria-hidden="true"></span>
    <span class="back-brand__name">Clear Crown</span>
  </div>
  <p class="back-tagline">Try Clear Crown Today and Be Lice Free Tomorrow!<br>All Natural In-Home Lice Removal Services</p>
  <div class="back-band">www.ClearCrownCare.com</div>
</section>

</body>
</html>
```